Kor'v Meridell Travel

We need a sleek, professional, inviting card to elicit global travel for the experienced and professional traveler. Royal blue, black and silver. (perhaps the wording could be silver with black shadow?-get creative) Maybe a watermark on the front and the full raised logo on the back.
We want a stylish and modern card, but professional.

```html
<!DOCTYPE html>
<html lang="en">
<head>
<meta charset="utf-8">
<title>Kor'v Meridell Travel – Business Card</title>
<link href="https://fonts.googleapis.com/css2?family=Josefin+Sans:wght@600&family=Arimo:wght@400&display=swap" rel="stylesheet">
<style>
  :root {
    --stage: #9a9a9a;
    --brand-blue: #22a7e0;
    --brand-green: #7dc242;
    --card-white: #ffffff;
    --ink: #1e1e1e;
    --rule: #9a9a9a;
  }
  * { box-sizing: border-box; margin: 0; padding: 0; }
  html, body { width: 1200px; height: 1200px; overflow: hidden; }
  body {
    background: var(--stage);
    position: relative;
    font-family: "Arimo", Arial, sans-serif;
  }
  .card {
    position: absolute;
    top: 304px;
    width: 366px;
    height: 594px;
    border-radius: 12px;
    overflow: hidden;
  }
  .card--back { left: 200px; background: var(--brand-blue); }
  .card--front { left: 599px; background: var(--card-white); text-align: center; color: var(--ink); }

  .wordmark {
    font-family: "Josefin Sans", "Helvetica Neue", sans-serif;
    font-weight: 600;
    text-transform: uppercase;
    line-height: 1;
  }
  .back-wordmark {
    position: absolute;
    left: 0; right: 0; top: 491px;
    color: var(--card-white);
    text-align: center;
  }
  .back-wordmark .name-line { font-size: 28px; }
  .tagline-row {
    display: flex;
    align-items: center;
    justify-content: center;
    gap: 10px;
    margin-top: 6px;
    font-size: 21px;
    letter-spacing: 5px;
  }
  .tagline-row .rule { width: 82px; height: 2px; background: currentColor; }

  .front-wordmark {
    position: absolute;
    left: 0; right: 0; top: 160px;
    color: var(--brand-blue);
  }
  .front-wordmark .name-line { font-size: 29px; }
  .front-wordmark .tagline-row .rule { width: 80px; }

  .person { position: absolute; left: 0; right: 0; top: 304px; }
  .person-name {
    font-family: "Josefin Sans", "Helvetica Neue", sans-serif;
    font-weight: 600;
    font-size: 23px;
    color: var(--brand-blue);
    text-transform: uppercase;
  }
  .person-title {
    margin-top: 6px;
    font-size: 15px;
    color: var(--brand-green);
    text-transform: uppercase;
  }

  .contact-icons {
    position: absolute; top: 364px; left: 0; right: 0;
    display: flex; align-items: center; justify-content: center; gap: 4px;
  }
  .contact-icons .rule { width: 36px; height: 1px; background: var(--rule); margin: 0 6px; }
  .icon-tile {
    width: 25px; height: 25px; border-radius: 4px; background: var(--brand-blue);
    display: flex; align-items: center; justify-content: center;
  }
  .icon-tile svg { width: 16px; height: 16px; }

  .contact-list {
    position: absolute; top: 400px; left: 0; right: 0;
    font-size: 16.5px; line-height: 21.7px;
  }
  .contact-list .link { color: var(--brand-blue); }
  .divider { position: absolute; top: 496px; left: 88px; width: 195px; height: 1px; background: var(--rule); }
  .address { position: absolute; top: 508px; left: 0; right: 0; font-size: 16.5px; line-height: 21.7px; }
</style>
</head>
<body>
  <section class="card card--back" aria-label="Card back">
    <div class="back-wordmark wordmark">
      <div class="name-line">Kor'v Meridell</div>
      <div class="tagline-row"><span class="rule"></span><span>Travel</span><span class="rule"></span></div>
    </div>
  </section>

  <section class="card card--front" aria-label="Card front">
    <div class="front-wordmark wordmark">
      <div class="name-line">Kor'v Meridell</div>
      <div class="tagline-row"><span class="rule"></span><span>Travel</span><span class="rule"></span></div>
    </div>

    <div class="person">
      <div class="person-name">Elias Brandt</div>
      <div class="person-title">Managing Director</div>
    </div>

    <div class="contact-icons">
      <span class="rule"></span>
      <span class="icon-tile" aria-label="Phone">
        <svg viewBox="0 0 16 16" fill="none" stroke="#fff" stroke-width="1.4" stroke-linejoin="round"><path d="M2 6c0-2 2-3 6-3s6 1 6 3l-2 1-1-2H5L4 7z"/><rect x="3.5" y="8" width="9" height="5" rx="1"/></svg>
      </span>
      <span class="icon-tile" aria-label="Mobile">
        <svg viewBox="0 0 16 16" fill="none" stroke="#fff" stroke-width="1.4"><rect x="4.5" y="1.5" width="7" height="13" rx="1.2"/><line x1="7" y1="12.3" x2="9" y2="12.3"/></svg>
      </span>
      <span class="icon-tile" aria-label="Email">
        <svg viewBox="0 0 16 16" fill="none" stroke="#fff" stroke-width="1.4"><rect x="1.5" y="3.5" width="13" height="9"/><path d="M1.5 3.5 8 9l6.5-5.5M1.5 12.5 6 7.5M14.5 12.5 10 7.5"/></svg>
      </span>
      <span class="icon-tile" aria-label="Location">
        <svg viewBox="0 0 16 16" fill="#fff"><path d="M8 1a5 5 0 0 0-5 5c0 3.5 5 9 5 9s5-5.5 5-9a5 5 0 0 0-5-5zm0 7a2 2 0 1 1 0-4 2 2 0 0 1 0 4z"/></svg>
      </span>
      <span class="rule"></span>
    </div>

    <div class="contact-list">
      <div>044-123 456 789</div>
      <div>044-123 456 789</div>
      <div>hello@korvmeridell.com</div>
      <div>www.<span class="link">korvmeridell</span>.com</div>
    </div>
    <div class="divider"></div>
    <div class="address">
      <div>421, Address line here</div>
      <div>45452,Country Name</div>
    </div>
  </section>
</body>
</html>
```